BRTL web site redesign

Coastal Linkage Engineering service (BRTL) is a diverse technology company specialising in design and installation of fibre optics, network convergence and building services, for commercial clients in Australia, we required a new design of our website to attract new clients, generate sales leads, and provide information about our services to the market. The site and should have a new technology look and feel and be designed in word press. our branding colour is blue.

Target Market(s)

New developments, Construction organisations, Commercial end users, IT managers, Consultants.

Industry/Entity Type

It Company

Number of Pages Required

5+ page

Font styles to use
Sans Serif

Colors
0292cd
3176b5

Requirements
Must have
• key pages.
• Home page with some sizzle, automated pictures running through, I like the look of this competitor website http://www.gleamwirex.com.au/ good clean menus and easy to navigate.
• Services page our key services are Fibre optics, Security, Building services,Electrical. I would like the same page layout (Design) for all our services, with a find out more link on each page, manly picture driven with text around our key messaging.
• About us page with space for company profile and directors pictures, bio and contact information.
• Certifications / Accreditations page with have over 20 certifications on different products from suppliers, and a number of licences from governing bodies.
• Current and past projects page with case studies and customer outcomes
• Contact us page with options around what services they require more information on, please keep in mind the site is around generating sales Leeds and being seen as an industry expert.
Nice to have
• RSS feeds, Linked in link, to be placed within the design, Consistent BRTL branding,Same colour blue as our logo Document library for education information, white papers, presentations etc,
• a new technology look and feel, mobile friendly.
Should not have
• boring layout, move away from our cuurent website http://www.brtlgroup.com.au/
• no e eCommerce store required.

```html
<!DOCTYPE html>
<html lang="en">
<head>
<meta charset="utf-8">
<title>BRTL – Coastal Linkage Engineering service</title>
<link rel="stylesheet" href="https://fonts.googleapis.com/css2?family=Roboto:wght@300;400;500;700&display=swap">
<style>
:root{
  --brand:#0292cd;
  --brand-deep:#3176b5;
  --topbar:#0a86bf;
  --nav-dark:#1e1e1e;
  --nav-mid:#3a3a3a;
  --text:#555;
  --text-light:#777;
  --panel:#f0f0f0;
  --footer:#101010;
  --white:#fff;
}
*{margin:0;padding:0;box-sizing:border-box}
html,body{width:706px;height:1200px;overflow:hidden;background:var(--white)}
body{position:relative;font-family:'Roboto',Arial,sans-serif;color:var(--text)}
.abs{position:absolute}

.topbar{left:0;top:0;width:706px;height:35px;background:var(--topbar)}
.topbar .phone{left:548px;top:12px;font-size:8px;color:var(--white);display:flex;align-items:center;gap:4px}
.topbar .signin{left:618px;top:11px;width:37px;height:16px;border:1px solid var(--white);border-radius:3px;color:var(--white);font-size:6.5px;line-height:14px;text-align:center}

.navbar{left:0;top:35px;width:706px;height:38px;background:linear-gradient(#444,#1b1b1b)}
.nav{top:50px;display:flex;font-size:7.5px;color:var(--white);text-transform:uppercase}
.nav span{position:absolute;white-space:nowrap}
.nav .active{color:var(--brand)}

.logo{left:53px;top:9px;width:126px;height:63px;background:var(--white);padding:3px;z-index:3}
.logo-inner{width:100%;height:100%;background:var(--brand-deep);display:flex;flex-direction:column;justify-content:center;align-items:center}
.logo-name{font-size:30px;font-weight:700;color:var(--white);letter-spacing:1px;line-height:1}
.logo-sub{font-size:4.6px;color:var(--white);margin-top:4px;text-transform:uppercase;letter-spacing:.2px}

.dropdown{left:306px;top:73px;width:88px;height:63px;background:rgba(2,146,205,.9);z-index:3;padding:6px 0 0 12px;font-size:7px;color:var(--white);line-height:13.4px}
.dropdown li{list-style:none}
.dropdown li::before{content:"›";margin-right:5px}

.hero{left:0;top:73px;width:706px;height:301px;background:linear-gradient(100deg,#3c6e3a 0%,#5a5a4e 25%,#3b3f48 50%,#23262c 70%,#3b6f9a 100%)}
.hero-title{left:80px;top:176px;font-size:35px;font-weight:500;color:var(--white);text-shadow:0 1px 3px rgba(0,0,0,.5)}
.hero-sub{left:80px;top:219px;font-size:22px;font-weight:300;color:var(--white);text-shadow:0 1px 3px rgba(0,0,0,.5)}
.hero-arrow{top:192px}

.welcome-title{left:0;top:398px;width:706px;text-align:center;font-size:14px;color:var(--brand-deep)}
.welcome-text{left:60px;top:424px;width:586px;text-align:center;font-size:8.1px;line-height:15.6px;color:var(--text)}
.btn-primary{left:318px;top:482px;width:70px;height:23px;background:linear-gradient(var(--brand),#1b7bb8);border:1px solid #0c6aa4;border-radius:2px;color:var(--white);font-size:7.5px;font-weight:500;text-align:center;line-height:21px}

.services{left:0;top:530px;width:706px;height:217px;background:linear-gradient(90deg,#1b7fb9,#2a8cc4 55%,#3c97cb)}
.services-title{left:0;top:549px;width:706px;text-align:center;font-size:16px;font-weight:500;color:var(--white)}
.service{top:584px;width:140px;text-align:center;color:var(--white)}
.service .ring{width:56px;height:56px;margin:0 auto;border-radius:50%;border:2px solid var(--white);padding:3px}
.service .ring div{width:100%;height:100%;border-radius:50%;background:var(--white);display:flex;align-items:center;justify-content:center}
.service h3{font-size:10px;font-weight:400;margin-top:9px}
.service p{font-size:6.2px;line-height:9px;margin-top:6px;padding:0 12px}
.service .btn-light{width:71px;height:20px;margin:7px auto 0;background:linear-gradient(#fff,#e2e2e2);border-radius:2px;color:#333;font-size:8px;line-height:20px;box-shadow:0 1px 2px rgba(0,0,0,.3)}

.card-photo{width:186px;height:102px;top:786px;border:3px solid var(--white);box-shadow:0 1px 5px rgba(0,0,0,.35)}
.card-title{top:905px;font-size:8px;font-weight:500;color:var(--brand-deep);text-transform:uppercase}
.card-text{top:920px;width:190px;font-size:7.2px;line-height:13px;color:var(--text-light)}

.info{left:0;top:982px;width:706px;height:128px;background:var(--panel)}
.info h4{position:absolute;top:1001px;font-size:10px;font-weight:400;color:var(--brand-deep)}
.contact{left:54px;top:1024px;font-size:6px;line-height:11px;color:var(--text)}
.contact-line{display:flex;align-items:center;gap:6px;margin-top:2px}
.news-item{left:249px;display:flex;gap:9px}
.news-item .thumb{width:37px;height:29px;border:2px solid var(--white);box-shadow:0 0 2px rgba(0,0,0,.3)}
.news-item p{font-size:6px;line-height:10px;width:150px}
.news-item .date{color:var(--brand)}
.newsletter-text{left:491px;top:1026px;width:170px;font-size:7px;line-height:12px}
.subscribe-input{left:491px;top:1062px;width:127px;height:20px;background:var(--white);border:1px solid #ccc;font-size:6px;color:#999;padding-left:7px;line-height:18px}
.subscribe-btn{left:618px;top:1062px;width:34px;height:20px;background:var(--brand);color:var(--white);font-size:7px;font-weight:500;text-align:center;line-height:20px}

.footer{left:0;top:1110px;width:706px;height:90px;background:var(--footer)}
.footer-links{left:53px;top:1140px;font-size:7px;color:var(--white)}
.footer-copy{left:53px;top:1154px;font-size:7px;color:var(--white)}
.social-title{left:445px;top:1144px;font-size:7px;color:var(--white)}
.social-sub{left:445px;top:1157px;font-size:6px;color:var(--white)}
.social-dot{top:1140px;width:21px;height:21px;border-radius:50%;border:2px solid var(--white)}
</style>
</head>
<body>

<header>
  <div class="abs topbar"></div>
  <div class="abs topbar"><div class="abs phone">
    <svg width="8" height="8" viewBox="0 0 10 10"><rect width="10" height="10" rx="2" fill="#fff"/><path d="M3 2.5l1 1.5-.6.8a4 4 0 0 0 1.8 1.8l.8-.6 1.5 1-.6 1C4.5 8 2 5.5 2 3.1z" fill="#0a86bf"/></svg>
    1300 555 214</div>
    <div class="abs signin">SIGN IN</div>
  </div>
  <div class="abs navbar"></div>
  <div class="abs logo"><div class="logo-inner"><span class="logo-name">BRTL</span><span class="logo-sub">Coastal Linkage Engineering service</span></div></div>
  <nav class="abs nav">
    <span style="left:268px">Home</span>
    <span class="active" style="left:305px">Services ▾</span>
    <span style="left:363px">About us</span>
    <span style="left:415px">Certifications</span>
    <span style="left:495px">Current / Past projects</span>
    <span style="left:611px">Contact us</span>
  </nav>
  <ul class="abs dropdown">
    <li>Fibre optics</li><li>Security</li><li>Building services</li><li>Electrical</li>
  </ul>
</header>

<section>
  <div class="abs hero" role="img" aria-label="Close-up of a fibre optic fusion splicer with green fibre bundles"></div>
  <h1 class="abs hero-title">FIBRE OPTICS</h1>
  <p class="abs hero-sub">Installation and solutions</p>
  <svg class="abs hero-arrow" style="left:33px" width="20" height="40" viewBox="0 0 20 40"><path d="M18 1L2 20l16 19" fill="none" stroke="#fff" stroke-width="1.5"/></svg>
  <svg class="abs hero-arrow" style="left:652px" width="20" height="40" viewBox="0 0 20 40"><path d="M2 1l16 19L2 39" fill="none" stroke="#fff" stroke-width="1.5"/></svg>
</section>

<section>
  <h2 class="abs welcome-title">WELCOME TO BRTL GROUP</h2>
  <p class="abs welcome-text">Lorem Ipsum has been the industry's standard dummy text ever since the 1500s, when an unknown printer took a galley of type and scrambled it to make a type specimen book. It has survived not only five centuries, but also the leap into electronic typesetting, remaining essentially unchanged. It was popularised in the 1960s with the release of Letraset sheets containing Lorem Ipsum passages, and more recently with desktop publishing software</p>
  <div class="abs btn-primary">READ MORE</div>
</section>

<section>
  <div class="abs services" role="img" aria-label="Blue-tinted photo of a technician working at a server rack"></div>
  <h2 class="abs services-title">SERVICES</h2>
  <div class="abs service" style="left:44px">
    <div class="ring"><div><svg width="22" height="22" viewBox="0 0 24 24"><circle cx="9" cy="10" r="5" fill="none" stroke="#111" stroke-width="3" stroke-dasharray="2.2 1.6"/><circle cx="9" cy="10" r="2" fill="#111"/><circle cx="17" cy="17" r="3.5" fill="none" stroke="#111" stroke-width="2.5" stroke-dasharray="1.8 1.2"/><circle cx="18" cy="6" r="2.5" fill="none" stroke="#111" stroke-width="2"/></svg></div></div>
    <h3>FIBRE OPTICS</h3><p>Lorem Ipsum is simply dummy text of the printing and typesetting industry</p><div class="btn-light">Read More</div>
  </div>
  <div class="abs service" style="left:204px">
    <div class="ring"><div><svg width="18" height="20" viewBox="0 0 18 20"><path d="M4 9V6a5 5 0 0 1 10 0v3" fill="none" stroke="#111" stroke-width="2.5"/><rect x="1" y="9" width="16" height="11" rx="1.5" fill="#111"/></svg></div></div>
    <h3>SECURITY</h3><p>Lorem Ipsum is simply dummy text of the printing and typesetting industry</p><div class="btn-light">Read More</div>
  </div>
  <div class="abs service" style="left:364px">
    <div class="ring"><div><svg width="16" height="22" viewBox="0 0 16 22"><rect width="16" height="22" fill="#111"/><g fill="#fff"><rect x="3" y="3" width="3" height="2"/><rect x="10" y="3" width="3" height="2"/><rect x="3" y="7" width="3" height="2"/><rect x="10" y="7" width="3" height="2"/><rect x="3" y="11" width="3" height="2"/><rect x="10" y="11" width="3" height="2"/><rect x="6" y="16" width="4" height="6"/></g></svg></div></div>
    <h3>BUILDING SERVICES</h3><p>Lorem Ipsum is simply dummy text of the printing and typesetting industry</p><div class="btn-light">Read More</div>
  </div>
  <div class="abs service" style="left:524px">
    <div class="ring"><div><svg width="12" height="20" viewBox="0 0 12 20"><path d="M7 0L1 11h4l-2 9 8-12H7z" fill="#111"/></svg></div></div>
    <h3>ELECTRICAL</h3><p>Lorem Ipsum is simply dummy text of the printing and typesetting industry</p><div class="btn-light">Read More</div>
  </div>
</section>

<section>
  <div class="abs card-photo" style="left:54px;background:radial-gradient(circle at 70% 40%,#5fc7e0,#0f4c6b 55%,#04121c)" role="img" aria-label="Glowing fibre optic strands"></div>
  <div class="abs card-photo" style="left:261px;background:linear-gradient(90deg,#c85a12,#e57a22 50%,#8a6a4a)" role="img" aria-label="Row of orange electrical switchboards"></div>
  <div class="abs card-photo" style="left:467px;background:linear-gradient(135deg,#3a5f8e,#9db8d6 50%,#6e7f92)" role="img" aria-label="Collage of office towers and a security camera"></div>
  <h3 class="abs card-title" style="left:55px">Ipsum is simply dummy text</h3>
  <h3 class="abs card-title" style="left:261px">Ipsum is simply dummy text</h3>
  <h3 class="abs card-title" style="left:466px">Ipsum is simply dummy text</h3>
  <p class="abs card-text" style="left:55px">Lorem ipsum dolor sit amet, consectetur adipiscing elit. Sed blandit massa vel mauris sollicitudin dig issim. Phasellus ultrices tellus eget ipsum</p>
  <p class="abs card-text" style="left:261px">Lorem ipsum dolor sit amet, consectetur adipiscing elit. Sed blandit massa vel mauris sollicitudin dig issim. Phasellus ultrices tellus eget ipsum</p>
  <p class="abs card-text" style="left:466px">Lorem ipsum dolor sit amet, consectetur adipiscing elit. Sed blandit massa vel mauris sollicitudin dig issim. Phasellus ultrices tellus eget ipsum</p>
</section>

<section class="info-area">
  <div class="abs info"></div>
  <div class="info">
    <h4 style="left:52px">CONTACT INFO</h4>
    <h4 style="left:249px">LATEST NEWS</h4>
    <h4 style="left:491px">NEWSLETTER</h4>
  </div>
  <div class="abs contact">
    Suite 4B, 12 Harbour Crescent<br>Bayview NSW 2104<br>PO Box 2290 NSW 1630
    <div class="contact-line" style="margin-top:7px"><svg width="6" height="6" viewBox="0 0 10 10"><path d="M2 0l2 3-1 1.3a6 6 0 0 0 2.7 2.7L7 6l3 2-1 2C4 10 0 6 0 1z" fill="#3176b5"/></svg>1300 555 214</div>
    <div class="contact-line"><svg width="7" height="5" viewBox="0 0 14 10"><rect width="14" height="10" fill="#3176b5"/><path d="M0 0l7 5 7-5" fill="none" stroke="#fff" stroke-width="1.2"/></svg>hello@brtlgroup.com.au</div>
  </div>
  <div class="abs news-item" style="top:1023px">
    <div class="thumb" style="background:linear-gradient(135deg,#4f7d5a,#a7b9a0)" role="img" aria-label="Aerial view of a town"></div>
    <p>Lorem ipsum dolor sit amet, consectetur adipisicing elit, sed do eiusmod tempor<br><span class="date">july 7, 2015</span></p>
  </div>
  <div class="abs news-item" style="top:1063px">
    <div class="thumb" style="background:linear-gradient(135deg,#9cc7e0,#e2b7a6)" role="img" aria-label="Coastal town buildings"></div>
    <p>Lorem ipsum dolor sit amet, consectetur adipisicing elit, sed do eiusmod tempor<br><span class="date">july 7, 2015</span></p>
  </div>
  <p class="abs newsletter-text">Join our mailing list to stay up to date and get notices about our new releases!</p>
  <div class="abs subscribe-input">mail@example.com</div>
  <div class="abs subscribe-btn">JOIN</div>
</section>

<footer>
  <div class="abs footer"></div>
  <div class="abs footer-links">HOME &nbsp;|&nbsp; ABOUT &nbsp;|&nbsp; NEWS &nbsp;|&nbsp; BLOG &nbsp;|&nbsp; CONTACTS</div>
  <div class="abs footer-copy">© 2015 &nbsp;Privacy Policy</div>
  <div class="abs social-title">SOCIAL NETWORKS</div>
  <div class="abs social-sub">Lorem Ipsum is simply dummy text</div>
  <div class="abs social-dot" style="left:560px;background:#3b5998"></div>
  <div class="abs social-dot" style="left:585px;background:#d14836"></div>
  <div class="abs social-dot" style="left:610px;background:#2ba3e1"></div>
  <div class="abs social-dot" style="left:635px;background:#ef6a1c"></div>
</footer>

</body>
</html>
```